'Velunor' Nutritional supplements label design (UPDATED)

- 'Velunor' is a upscale health supplements brand
-The company will be packing the products in plastic bottles like other supplements
-Try to use a distinct design which is recognizable from distance
-Brand Logo is attached

-UPDATE- 2-

Label Dimensions and Design:

Hi Everyone,

Sorry for the late response caused by some very busy schedule.

Anyhow, here are the dimensions of the label (Self Adhesive) that we need:

Length of Label : 18cm
Height of Label : 6.5 cm

Product Names:

-Metabolism Formula
-Complete Multivitamins and Minerals (For Men, Women and Kids)
-Healthy Bones
-Skin Support
-Omega-3 oil for Healthy Heart

As for the ingredients just use Lorem Ipsum for now.

Many thanks to all of you in advance.

Target Market(s)

Middle Income families

Industry/Entity Type

Plastic

Requirements
Must have
• -Quality
-Effective
-Unique

```html
<!DOCTYPE html>
<html lang="en">
<head>
<meta charset="utf-8">
<title>Velunor Complete Multivitamins &amp; Minerals Label</title>
<link rel="stylesheet" href="https://fonts.googleapis.com/css2?family=Montserrat:wght@600;700&family=Kaushan+Script&family=Passion+One:wght@700&family=Lilita+One&family=Tinos:wght@400;700&display=swap">
<style>
  :root {
    --sun-core: #fffbe0;
    --sun-mid: #ffd43a;
    --sun-edge: #f6921e;
    --ribbon: #f26b1d;
    --ribbon-dark: #c9480f;
    --royal: #1d22c9;
    --band-blue: #1e28c8;
    --band-gold: #f3b51d;
    --kids-yellow: #fff200;
    --teal: #1fb3a6;
    --script-red: #e5141b;
    --count-red: #e0241c;
    --panel-bg: #fdfbd4;
    --panel-line: #cfd67a;
    --panel-frame: #e6c95a;
    --ink: #1a1a1a;
    --care-border: #ffe100;
  }
  * { margin: 0; padding: 0; box-sizing: border-box; }
  html, body { width: 1200px; height: 433px; overflow: hidden; background: #fff; }
  .label {
    position: relative; width: 1200px; height: 433px; overflow: hidden;
    font-family: "Montserrat", sans-serif;
  }
  .sunburst {
    position: absolute; inset: 0;
    background: radial-gradient(ellipse 60% 75% at 44% 48%, var(--sun-core) 0%, var(--sun-mid) 38%, var(--sun-edge) 85%);
  }
  .count {
    position: absolute; left: 86px; top: 40px; text-align: center; line-height: 1;
  }
  .count-number {
    display: inline-block; background: #fff; color: var(--count-red);
    font: 700 17px "Montserrat", sans-serif; padding: 1px 7px; border-radius: 10px;
  }
  .count-unit { display: block; color: var(--royal); font: 400 19px "Montserrat", sans-serif; margin-top: 1px; }
  .brand-mark {
    position: absolute; left: 330px; top: 118px; display: flex; align-items: center; gap: 18px;
  }
  .brand-dot { width: 56px; height: 56px; border-radius: 50%; background: var(--teal); }
  .brand-name { color: var(--teal); font: 600 82px/1 "Montserrat", sans-serif; letter-spacing: 4px; }
  .title-art { position: absolute; left: 330px; top: 200px; }
  .audience-band {
    position: absolute; left: 0; top: 362px; width: 1200px; height: 52px;
    background: var(--band-blue);
    border-top: 4px solid var(--band-gold); border-bottom: 4px solid var(--band-gold);
    box-shadow: 0 -3px 0 var(--band-blue), 0 3px 0 var(--band-blue);
  }
  .audience {
    position: absolute; left: 0; width: 900px; top: 367px; text-align: center;
    color: var(--kids-yellow); font: 400 31px/42px "Lilita One", sans-serif;
  }
  .info-panel {
    position: absolute; left: 944px; top: 18px; width: 236px; height: 340px;
    background: var(--panel-bg); border: 3px double var(--panel-frame);
  }
  .info-inner {
    position: absolute; left: 10px; top: 22px; width: 212px; height: 290px;
    border: 4px solid var(--panel-line);
    font-family: "Tinos", serif; color: var(--ink); font-size: 13px;
  }
  .spec { position: absolute; left: 8px; top: 10px; line-height: 20px; }
  .spec span { display: inline-block; width: 96px; }
  .ingredients { position: absolute; left: 0; width: 100%; top: 110px; text-align: center; line-height: 17px; }
  .maker { position: absolute; right: 14px; top: 190px; font: 700 8px "Montserrat", sans-serif; }
  .maker-name {
    position: absolute; left: 0; width: 100%; top: 205px; text-align: center;
    color: var(--teal); font: 600 19px "Montserrat", sans-serif; letter-spacing: 3px;
  }
  .care {
    position: absolute; left: 8px; top: 235px; width: 188px; height: 34px;
    background: #fff; border: 3px solid var(--care-border); text-align: center;
    font: 700 9.5px/12px "Montserrat", sans-serif; padding-top: 4px;
  }
</style>
</head>
<body>
<div class="label">
  <div class="sunburst" role="img" aria-label="Radiating sunburst background in yellow and orange"></div>

  <div class="count"><span class="count-number">270</span><span class="count-unit">Capsules</span></div>

  <div class="brand-mark"><span class="brand-dot"></span><span class="brand-name">VELUNOR</span></div>

  <svg class="title-art" width="560" height="140" viewBox="0 0 560 140">
    <path d="M10 60 Q250 30 545 72 L535 118 Q250 80 20 112 Z" fill="var(--ribbon)" stroke="var(--ribbon-dark)" stroke-width="2"/>
    <text x="375" y="50" transform="rotate(-8 450 40)" font-family="Kaushan Script, cursive" font-size="44" fill="var(--script-red)" stroke="#fff" stroke-width="2" paint-order="stroke">Complete</text>
    <text x="40" y="118" transform="rotate(-4 280 100)" font-family="Passion One, sans-serif" font-weight="700" font-size="50" fill="var(--royal)" stroke="#fff" stroke-width="5" paint-order="stroke" letter-spacing="0.5">Multivitamins &amp; Minerals</text>
  </svg>

  <div class="audience-band"></div>
  <div class="audience">For Men,Women and Kids</div>

  <div class="info-panel">
    <div class="info-inner">
      <div class="spec">
        <div><span>Net Weight</span>:</div>
        <div><span>Date of Mfg.</span>:</div>
        <div><span>Date of Expiry</span>:</div>
        <div>Keep in a cool &amp; dry place.</div>
      </div>
      <div class="ingredients">Ingredients:<br>Lorem Ipsum</div>
      <div class="maker">Manufactured By:</div>
      <div class="maker-name">VELUNOR</div>
      <div class="care">Customer Care No.<br>XXX XXXXXXXXXX</div>
    </div>
  </div>
</div>
</body>
</html>
```